Moravel Aesthetic Doctor

I require an elegant, luxurious looking business card for my aesthetic business. I am a doctor and that will set me aside from competitors. I am planning to provide home and spa based treatments to clients with high expectations. I have attached my logo.

```html
<!DOCTYPE html>
<html lang="en">
<head>
<meta charset="utf-8">
<title>Moravel Aesthetic Doctor – Business Card</title>
<link href="https://fonts.googleapis.com/css2?family=Montserrat:wght@400;500&display=swap" rel="stylesheet">
<style>
  :root {
    --backdrop: #3a3a3c;
    --card: #1d1d1f;
    --sky: #4fb3e8;
    --silver: #aab0bd;
    --white: #ffffff;
    --slate: #8d94a3;
  }
  * { margin: 0; padding: 0; box-sizing: border-box; }
  html, body { width: 799px; height: 1200px; overflow: hidden; }
  body {
    background: var(--backdrop);
    font-family: "Montserrat", sans-serif;
    position: relative;
  }
  .card {
    position: absolute;
    left: 90px;
    width: 620px;
    height: 354px;
    background: var(--card);
    border-radius: 4px;
    overflow: hidden;
    box-shadow: 0 14px 30px rgba(0,0,0,0.45);
  }
  .card--front { top: 150px; }
  .card--back { top: 700px; }

  .brand-name {
    position: absolute;
    font-family: "Montserrat", sans-serif;
    font-weight: 500;
    color: var(--white);
  }
  .card--front .brand-name {
    left: 0; right: 0; top: 92px;
    text-align: center;
    font-size: 32px;
    line-height: 40px;
  }

  .services {
    position: absolute; left: 0; right: 0; top: 200px;
    text-align: center; color: var(--white);
    font-size: 17px; line-height: 26px;
  }
  .services span { margin: 0 10px; }
  .ribbon {
    position: absolute; left: 0; right: 0; top: 268px; height: 36px;
    background: var(--sky); color: var(--white);
    font-size: 17px; letter-spacing: 1px;
    display: flex; align-items: center; justify-content: center;
  }

  .person { position: absolute; left: 36px; top: 32px; }
  .person__name { color: var(--silver); font-size: 22px; }
  .person__cred { color: var(--sky); font-size: 10px; font-style: italic; margin-top: 2px; }
  .person__diploma { color: var(--sky); font-size: 14px; line-height: 17px; margin-top: 4px; }

  .contact {
    position: absolute; left: 36px; top: 148px;
    color: var(--white); font-size: 13px; line-height: 20px;
  }
  .contact li { list-style: none; display: flex; align-items: center; gap: 8px; }
  .contact svg { width: 12px; height: 12px; fill: var(--white); }
  .social-dot { width: 13px; height: 13px; border-radius: 50%; background: var(--white); display: inline-block; }
  .web { position: absolute; left: 250px; top: 208px; color: var(--white); font-size: 13px; display: flex; gap: 8px; align-items: center; }
  .web svg { width: 12px; height: 12px; }

  .card--back .brand-name {
    right: 34px; top: 98px;
    text-align: right;
    font-size: 24px;
    line-height: 30px;
  }

  .waves { position: absolute; left: 0; top: 0; width: 620px; height: 354px; }
  .slogan {
    position: absolute; right: 34px; bottom: 28px;
    color: var(--white); font-size: 19px; line-height: 24px; text-align: right;
  }
</style>
</head>
<body>

<section class="card card--front">
  <div class="brand-name">Moravel Aesthetic Doctor</div>
  <div class="services">
    <div>Dermal Injectables<span>|</span>Plasma Facials<span>|</span>Microneedling</div>
    <div>Skin Boosters<span>|</span>Excessive Sweating</div>
  </div>
  <div class="ribbon">HOME AND SPA BASED TREATMENTS</div>
</section>

<section class="card card--back">
  <svg class="waves" viewBox="0 0 620 354" aria-hidden="true">
    <path d="M0 232 C120 190 250 250 380 270 C480 285 560 260 620 240 L620 354 L0 354 Z" fill="var(--slate)"/>
    <path d="M0 246 C120 206 250 262 380 282 C480 297 560 272 620 254 L620 354 L0 354 Z" fill="var(--card)"/>
    <path d="M0 262 C110 230 240 282 370 298 C470 310 560 290 620 274 L620 354 L0 354 Z" fill="var(--sky)"/>
  </svg>

  <div class="person">
    <div class="person__name">Dr Elena Varga</div>
    <div class="person__cred">MRCPCH MD</div>
    <div class="person__diploma">Australasian Diploma of<br>Aesthetic Medicine</div>
  </div>

  <ul class="contact">
    <li><svg viewBox="0 0 12 12"><path d="M0 2h12v8H0z M0 2l6 4 6-4" stroke="var(--card)" stroke-width="1"/></svg>elena@moravel.co.nz</li>
    <li><svg viewBox="0 0 12 12"><path d="M2 0l3 3-1.5 1.5a7 7 0 0 0 4 4L9 7l3 3-2 2C5 12 0 7 0 2z"/></svg>0800 555 014</li>
    <li>Follow us on: <span class="social-dot"></span><span class="social-dot"></span></li>
  </ul>
  <div class="web">
    <svg viewBox="0 0 12 12" fill="none" stroke="var(--white)" stroke-width="1"><circle cx="6" cy="6" r="5.3"/><ellipse cx="6" cy="6" rx="2.3" ry="5.3"/><path d="M0.7 6h10.6"/></svg>
    www.moravel.co.nz
  </div>

  <div class="brand-name">Moravel<br>Aesthetic Doctor</div>

  <div class="slogan">Home and Spa<br>Based Treatments</div>
</section>

</body>
</html>
```